BRAMBLE is looking for a design partner

We are a group of videographers, photographers and editors currently rebranding our company. Originally Marcus Kelloway Photography, we have grown over the years into a company that does a lot of different things for a variety of corporate clients. It's clear the company is no longer Marcus, but a whole team. We have submitted a design contest for our new logo, purchased our new URL/email, and are now looking to get things moving on the website. We have most copy ready and are looking to help move online. The site should load quickly, be mobile friendly, look modern, and be very easy to navigate. Our videos run on Vimeo so we need to make sure that we can embed or run videos from the Vimeo account.

We are excited to be starting this new chapter. Hopefully you can come along with us! Marcus

Target Market(s)

Businesses looking to see what we do, examples of our work, and who we are.

Industry/Entity Type

Multimedia

Font styles to use
Serif
Sans Serif

Colors
33a6d7
3176b5
ffffff

Requirements
Must have
• I believe we are looking for a bright white background website.

Here is a list of areas that we will need to have on the site.
-Overview video near top
-Our Mission
-Details of services
-About the team
-Our History (3 sections: Different from Start, Growth, Transformation)
-Working at BRAMBLE (area for talent and freelancer to see employment info, current opening, how to apply
-Internship Program details
-Contact Form
-FAQ
Nice to have
• Social media links, slideshow, etc
We need photo and videos sprinkled throughout the site to give it as modern a look as possible. I am open to using this for backgrounds or to segment sections. See our current site here marcuskellowayphotography.com/business/
Should not have
• Cannot load slow. This is our current challenge. Any thing we can do to move this along will be helpful.

```html
<!DOCTYPE html>
<html lang="en">
<head>
<meta charset="utf-8">
<title>BRAMBLE — Creative Collective</title>
<link rel="stylesheet" href="https://fonts.googleapis.com/css2?family=Montserrat:wght@700;800&family=Poppins:wght@600&family=Arimo:wght@400;700&display=swap">
<style>
  :root {
    --page-bg: #eeeeee;
    --ink: #222222;
    --white: #ffffff;
    --brand-sky: #33a6d7;
    --brand-blue: #3176b5;
    --dash-light: #a3d5ee;
    --dash-mid: #4a88c4;
    --button-blue: #6597c7;
    --photo-deep: #2f4f7f;
    --photo-mid: #4a73a8;
    --photo-light: #6b91c2;
  }
  * { margin: 0; padding: 0; box-sizing: border-box; }
  html, body { width: 1200px; height: 664px; overflow: hidden; background: var(--page-bg); }
  .hero { position: relative; width: 1200px; height: 664px; overflow: hidden; background: var(--page-bg); }
  .hero-art { position: absolute; inset: 0; }
  .brand { position: absolute; left: 88px; top: 70px; display: flex; flex-direction: column; align-items: center; }
  .brand-dot { width: 56px; height: 56px; border-radius: 50%; background: var(--brand-sky); margin-bottom: 6px; }
  .brand-name { font-family: "Montserrat", sans-serif; font-weight: 800; font-size: 40px; color: var(--ink); letter-spacing: -1.5px; line-height: 1; }
  .main-nav { position: absolute; top: 61px; left: 743px; display: flex; }
  .main-nav a { font-family: "Poppins", sans-serif; font-weight: 600; font-size: 18px; color: var(--white); text-decoration: none; }
  .main-nav a:nth-child(1) { margin-right: 42px; }
  .main-nav a:nth-child(2) { margin-right: 44px; }
  .main-nav a:nth-child(3) { margin-right: 34px; }
  .headline { position: absolute; left: 68px; top: 204px; font-family: "Montserrat", sans-serif; font-weight: 800; font-size: 67px; line-height: 60px; color: var(--ink); letter-spacing: -1px; }
  .intro { position: absolute; left: 74px; top: 329px; font-family: "Arimo", sans-serif; font-size: 23px; line-height: 29.5px; color: var(--ink); }
  .intro strong { font-family: "Montserrat", sans-serif; font-weight: 800; letter-spacing: -0.5px; }
  .cta { position: absolute; left: 69px; top: 449px; width: 236px; height: 64px; border-radius: 32px; background: var(--button-blue); color: var(--white); font-family: "Montserrat", sans-serif; font-weight: 800; font-size: 21px; letter-spacing: -0.5px; display: flex; align-items: center; justify-content: center; text-decoration: none; }
  .social { position: absolute; left: 77px; top: 569px; display: flex; gap: 0; }
  .social a { display: block; width: 38px; height: 38px; border-radius: 50%; background: var(--brand-blue); }
  .social a:nth-child(1) { margin-right: 16px; }
  .social a:nth-child(2) { margin-right: 18px; }
  .social a:nth-child(3) { margin-right: 14px; }
</style>
</head>
<body>
<main class="hero">
  <svg class="hero-art" width="1200" height="664" viewBox="0 0 1200 664" aria-hidden="false">
    <defs>
      <linearGradient id="photo-tone" x1="0" y1="0" x2="1" y2="1">
        <stop offset="0" stop-color="var(--photo-light)"/>
        <stop offset="0.5" stop-color="var(--photo-mid)"/>
        <stop offset="1" stop-color="var(--photo-deep)"/>
      </linearGradient>
    </defs>
    <path class="hero-photo" role="img" aria-label="Photographer holding a camera at a desk with lenses and a laptop, in blue duotone"
      fill="url(#photo-tone)"
      d="M447 0 C430 60 445 130 500 165 C560 205 620 220 640 300 C660 380 655 450 680 520 C705 590 760 615 850 616 C940 617 990 570 1040 530 C1090 495 1150 490 1200 500 L1200 0 Z"/>
    <circle class="accent-circle" cx="1143" cy="624" r="89" fill="var(--brand-sky)"/>
    <g class="dashes-light" fill="var(--dash-light)">
      <rect x="314" y="102" width="103" height="14" rx="7"/>
      <rect x="385" y="149" width="25" height="14" rx="7"/>
      <rect x="416" y="149" width="103" height="14" rx="7"/>
    </g>
    <g class="dashes-mid" fill="var(--dash-mid)">
      <rect x="610" y="436" width="103" height="14" rx="7"/>
      <rect x="511" y="472" width="103" height="14" rx="7"/>
      <rect x="620" y="472" width="25" height="14" rx="7"/>
      <rect x="602" y="507" width="78" height="14" rx="7"/>
      <rect x="977" y="562" width="77" height="14" rx="7"/>
      <rect x="1037" y="593" width="77" height="14" rx="7"/>
    </g>
  </svg>

  <div class="brand">
    <span class="brand-dot"></span>
    <span class="brand-name">bramble</span>
  </div>

  <nav class="main-nav">
    <a href="#portfolio">Portfolio</a>
    <a href="#services">Services</a>
    <a href="#about">About</a>
    <a href="#contact">Contact</a>
  </nav>

  <h1 class="headline">CREATIVE<br>COLLECTIVE</h1>

  <p class="intro">
    We are content architects, engineers, and artists.<br>
    <strong>bramble</strong> is not just for meeting today’s challenge.<br>
    We are your partner for success
  </p>

  <a class="cta" href="#about">LEARN MORE</a>

  <div class="social">
    <a href="#" aria-label="Photo sharing profile"></a>
    <a href="#" aria-label="Community page"></a>
    <a href="#" aria-label="Short updates feed"></a>
    <a href="#" aria-label="Messaging contact"></a>
  </div>
</main>
</body>
</html>
```